Coral Bay Pools New website

I currently operate a swimming pool service and repair business and looking for a re design for my website as it has been over 5 years since it was designed. current site is coralbaypoolslv.com

```html
<!DOCTYPE html>
<html lang="en">
<head>
<meta charset="utf-8">
<title>Coral Bay Pools</title>
<link rel="stylesheet" href="https://fonts.googleapis.com/css2?family=Montserrat:wght@400;500;600&family=Outfit:wght@500;600&display=swap">
<style>
:root{
  --navy:#1f3f8a;
  --ink:#222a33;
  --orange:#f8a11b;
  --deep:#0b5a94;
  --sky:#39a3db;
  --crest:#1d4d8f;
  --footer:#1b2433;
  --white:#ffffff;
  --line:#c9ced6;
}
*{box-sizing:border-box;margin:0;padding:0}
html,body{width:1200px;height:3732px;overflow:hidden;background:var(--white)}
body{font-family:"Montserrat",sans-serif;color:var(--ink)}
.page{position:relative;width:1200px;height:3732px;overflow:hidden}
.abs{position:absolute}
h1,h2,h3,.brand{font-family:"Outfit",sans-serif;font-weight:600}
.btn{position:absolute;display:flex;align-items:center;justify-content:center;background:var(--orange);color:var(--white);border-radius:20px;font-size:12px;font-weight:600;letter-spacing:.3px;text-transform:uppercase}
.photo{position:absolute}
.site-header{position:absolute;left:0;top:0;width:1200px;height:64px;background:var(--white);z-index:5;box-shadow:0 1px 3px rgba(0,0,0,.08)}
.brand{position:absolute;left:162px;top:18px;display:flex;align-items:center;gap:8px;font-size:20px;color:var(--navy)}
.brand .dot{width:22px;height:22px;border-radius:50%;background:var(--orange)}
.main-nav{position:absolute;top:24px;font-size:13px;color:#4a5563}
.main-nav.active{color:var(--navy);font-weight:600}
.hero-photo{left:0;top:64px;width:1200px;height:540px;background:linear-gradient(135deg,#2f6fa3 0%,#3f97c4 40%,#5fb7d6 65%,#2c7fb0 100%)}
.hero-card{left:116px;top:177px;width:612px;height:246px;background:rgba(255,255,255,.88);border-radius:28px;padding:36px 42px}
.hero-card h1{font-size:37px;line-height:45px;color:var(--navy)}
.hero-card p{margin-top:12px;font-size:14px;color:#3a4350}
.circle{position:absolute;border-radius:50%;border:5px solid var(--white);box-shadow:0 6px 16px rgba(0,0,0,.25)}
.centered{position:absolute;left:0;width:1200px;text-align:center}
.section-title{font-size:34px;color:var(--ink)}
.about-text{left:230px;width:740px;text-align:center;font-size:13px;line-height:16.3px;color:#333b45}
.why-left{left:0;top:1040px;width:600px;height:500px;background:var(--deep)}
.why-photo{left:600px;top:1014px;width:600px;height:540px;background:linear-gradient(180deg,#8fb0c4 0%,#b8a58a 45%,#3fb3d9 75%,#1a8fc4 100%)}
.why-title{left:85px;top:1168px;font-size:34px;color:var(--white)}
.why-text{left:85px;top:1224px;width:400px;font-size:13px;line-height:18.2px;color:var(--white)}
.services-bg{left:0;top:1530px;width:1200px;height:700px;background:var(--sky)}
.card-img{position:absolute;top:1698px;width:350px;height:278px;border-radius:12px;border:3px solid rgba(255,255,255,.6)}
.card-title{position:absolute;top:1998px;width:350px;text-align:center;font-size:18px;color:var(--white)}
.card-title.orange{color:#ffcf7a}
.card-text{position:absolute;top:2036px;width:310px;text-align:center;font-size:12px;line-height:16px;color:var(--white)}
.field{position:absolute;border:1px solid var(--line);border-radius:25px;font-size:11px;color:#555;padding:17px 26px}
.field.area{border-radius:14px}
.banner-photo{left:0;top:2830px;width:1200px;height:560px;background:linear-gradient(120deg,#8a5a3a 0%,#b98a63 30%,#3f6f93 60%,#1f5585 100%)}
.banner-box{left:348px;top:2979px;width:505px;height:243px;background:rgba(40,75,150,.82);border-radius:14px}
.banner-box h2{position:absolute;left:0;top:26px;width:505px;text-align:center;font-size:54px;line-height:62px;color:var(--white)}
.site-footer{left:0;top:3340px;width:1200px;height:392px;background:var(--footer)}
.foot-nav{position:absolute;top:3555px;font-size:13px;color:#e4e8ee}
.rule{position:absolute;left:163px;width:874px;height:1px;background:#36404f}
.contact-item{position:absolute;top:3628px;display:flex;align-items:center;gap:10px;font-size:13px;color:#e4e8ee}
.contact-item .ico{width:26px;height:26px;border-radius:50%;background:var(--orange);display:flex;align-items:center;justify-content:center}
.social{position:absolute;top:3634px;width:14px;height:14px;border-radius:50%;background:#e4e8ee}
</style>
</head>
<body>
<div class="page">

<header class="site-header">
  <div class="brand"><span class="dot"></span>Coral Bay Pools</div>
  <span class="main-nav active" style="left:470px">Home</span>
  <span class="main-nav" style="left:572px">About Us</span>
  <span class="main-nav" style="left:690px">Our Services &#8964;</span>
  <span class="main-nav" style="left:833px">Free Estimate</span>
  <span class="main-nav" style="left:985px">Contact</span>
</header>

<section class="hero">
  <div class="photo hero-photo" role="img" aria-label="Tiled resort pool with hot tub, lounge chairs and umbrella"></div>
  <svg class="abs" style="left:0;top:520px" width="1200" height="120" viewBox="0 0 1200 120">
    <path d="M0 50 C200 90 420 80 620 60 C820 40 1000 20 1200 55 L1200 120 L0 120Z" fill="#39a3db"/>
    <path d="M0 58 C200 100 420 92 620 74 C820 56 1000 40 1200 70 L1200 120 L0 120Z" fill="#ffffff"/>
  </svg>
  <div class="abs hero-card">
    <h1>Welcome Nevada’s Top Rated Neighborhood Pool Cleaning</h1>
    <p>When you need professional pool cleaning services in Nevada.</p>
  </div>
  <div class="btn" style="left:161px;top:349px;width:140px;height:33px">Free Estimate</div>
  <div class="circle" role="img" aria-label="Woman in a sun hat relaxing in a pool" style="left:718px;top:347px;width:334px;height:334px;background:linear-gradient(160deg,#7cc7d8,#2aa6c9 60%,#1886b3)"></div>
  <div class="circle" role="img" aria-label="Technician cleaning a pool with a brush" style="left:860px;top:261px;width:208px;height:208px;background:linear-gradient(160deg,#8ba3b5,#2b5a9a 55%,#3aa8d8)"></div>
</section>

<section class="about">
  <h2 class="centered section-title" style="top:745px">Welcome About Us</h2>
  <p class="abs about-text" style="top:796px">When you need professional pool cleaning services in Nevada, you can count on the professionals at Coral Bay Pools to provide you with superior and prompt solutions. Whether you need assistance with a residential or commercial pool, we’ll vacuum, brush, and thoroughly clean your pool so it’s swim-ready. We’ll also clean your pool filters and inform you of any issues that arise. Our staff is certified by the Desert Valley Water Safety Board to ensure proper chemical levels and equipment are safe. To learn more about our pool cleaning services or to get your free estimate, contact our pool experts today.</p>
  <div class="btn" style="left:541px;top:913px;width:118px;height:33px">Learn More</div>
</section>

<section class="why">
  <div class="abs why-left"></div>
  <div class="photo why-photo" role="img" aria-label="Man jumping into a backyard pool with a splash"></div>
  <svg class="abs" style="left:0;top:1000px" width="1200" height="70" viewBox="0 0 1200 70">
    <path d="M0 40 L0 70 L600 70 L600 40 C450 5 200 5 60 30Z" fill="#39a3db"/>
    <path d="M600 14 C760 -4 980 0 1200 36 L1200 0 L600 0Z" fill="#ffffff"/>
  </svg>
  <div class="abs why-title"><h2 style="font-size:34px">Why Choose Us?</h2></div>
  <p class="abs why-text">Our full-service pool company proudly serves the entire Las Vegas valley, and we’re certified by the Desert Valley Water Safety Board to maintain the highest level of pool safety. If you need repairs, maintenance, scheduled cleanings, or any other pool services, contact us online or by phone today.</p>
  <div class="btn" style="left:85px;top:1354px;width:133px;height:33px">Contact Us</div>
</section>

<section class="services">
  <div class="abs services-bg"></div>
  <svg class="abs" style="left:0;top:1500px" width="1200" height="60" viewBox="0 0 1200 60">
    <path d="M0 20 C150 50 300 55 600 40 C800 30 1000 60 1200 55 L1200 60 L0 60Z" fill="#39a3db"/>
    <path d="M0 20 C150 50 300 55 600 45 L600 60 L0 60Z" fill="#39a3db"/>
  </svg>
  <h2 class="centered section-title" style="top:1608px;color:var(--white)">Our Services</h2>

  <div class="card-img" role="img" aria-label="Technician vacuuming a pool" style="left:48px;background:linear-gradient(160deg,#5b7a6a,#2a4a6a 50%,#3fb0d0)"></div>
  <h3 class="card-title" style="left:48px">Pool Services</h3>
  <p class="card-text" style="left:68px">When you invested in your pool, you knew it was a long-term investment in both money and time. At home, it’s an oasis.</p>
  <div class="btn" style="left:156px;top:2103px;width:133px;height:32px">Learn More</div>

  <div class="card-img" role="img" aria-label="Commercial pool with lounge chairs and umbrellas" style="left:423px;background:linear-gradient(180deg,#8a9aa0,#6b6a66 40%,#7ec7e3 60%,#3aa5d8)"></div>
  <h3 class="card-title" style="left:423px">Commercial Pool</h3>
  <p class="card-text" style="left:443px">As a commercial property owner or manager, doing your job well requires you to be mindful of all the details.</p>
  <div class="btn" style="left:532px;top:2103px;width:133px;height:32px">Learn More</div>

  <div class="card-img" role="img" aria-label="Residential pool surrounded by palm trees" style="left:800px;background:linear-gradient(180deg,#6f8f5a,#3f6b3a 45%,#2bb6dc 70%,#19a0d0)"></div>
  <h3 class="card-title orange" style="left:800px">Residential Pool</h3>
  <p class="card-text" style="left:820px">Here in Southern Nevada, you know it can get really, really hot. That’s why you your pool at off and relax with family and friends.</p>
  <div class="btn" style="left:908px;top:2103px;width:133px;height:32px">Learn More</div>

  <svg class="abs" style="left:0;top:2200px" width="1200" height="110" viewBox="0 0 1200 110">
    <path d="M0 0 L1200 0 L1200 50 C1050 20 850 10 620 55 C420 95 200 105 0 60Z" fill="#39a3db"/>
    <path d="M620 55 C800 15 1000 10 1200 50 L1200 56 C1050 40 900 50 700 85 C670 80 640 68 620 55Z" fill="#1d4d8f"/>
  </svg>
</section>

<section class="contact">
  <h2 class="centered section-title" style="top:2354px">Get In Touch</h2>
  <div class="field" style="left:191px;top:2434px;width:402px;height:50px">First Name*</div>
  <div class="field" style="left:607px;top:2434px;width:403px;height:50px">Last Name*</div>
  <div class="field" style="left:191px;top:2499px;width:402px;height:50px">E-mail*</div>
  <div class="field" style="left:607px;top:2499px;width:403px;height:50px">Phone*</div>
  <div class="field area" style="left:191px;top:2566px;width:819px;height:135px">Message*</div>
  <div class="btn" style="left:519px;top:2733px;width:162px;height:33px">Send</div>
</section>

<section class="banner">
  <div class="photo banner-photo" role="img" aria-label="Technician cleaning a resort pool edge with a hose"></div>
  <svg class="abs" style="left:0;top:2820px" width="1200" height="60" viewBox="0 0 1200 60">
    <path d="M0 0 L1200 0 L1200 20 C1000 5 800 15 620 35 C450 10 250 0 0 30Z" fill="#ffffff"/>
    <path d="M620 35 C800 15 1000 5 1200 20 L1200 50 C1000 30 800 35 650 48Z" fill="#39a3db"/>
  </svg>
  <div class="abs banner-box">
    <h2>Summer 2026<br>Pool Dreams</h2>
  </div>
  <div class="btn" style="left:522px;top:3149px;width:156px;height:33px">Free Estimate</div>
</section>

<footer>
  <div class="abs site-footer"></div>
  <svg class="abs" style="left:0;top:3290px" width="1200" height="90" viewBox="0 0 1200 90">
    <path d="M0 0 L1200 0 L1200 45 C1000 20 800 25 600 50 C400 75 200 80 0 60Z" fill="#1f5585"/>
    <path d="M0 60 C200 80 400 75 600 50 C800 25 1000 20 1200 45 L1200 90 L0 90Z" fill="#1b2433"/>
    <path d="M0 58 C200 78 400 73 600 48 L600 52 C400 80 200 86 0 66Z" fill="#39a3db"/>
  </svg>
  <div class="brand" style="left:0;top:3440px;width:1200px;justify-content:center;color:var(--white);font-size:24px"><span class="dot"></span>Coral Bay Pools</div>
  <span class="foot-nav" style="left:302px">Home</span>
  <span class="foot-nav" style="left:410px">About Us</span>
  <span class="foot-nav" style="left:535px">Our Services</span>
  <span class="foot-nav" style="left:684px">Free Estimate</span>
  <span class="foot-nav" style="left:841px">Contact</span>
  <div class="rule" style="top:3604px"></div>
  <div class="contact-item" style="left:221px"><span class="ico"><svg width="12" height="12" viewBox="0 0 24 24"><path d="M6.6 10.8a15 15 0 0 0 6.6 6.6l2.2-2.2a1 1 0 0 1 1-.25 11.4 11.4 0 0 0 3.6.57 1 1 0 0 1 1 1V20a1 1 0 0 1-1 1A17 17 0 0 1 3 4a1 1 0 0 1 1-1h3.5a1 1 0 0 1 1 1c0 1.25.2 2.45.57 3.57a1 1 0 0 1-.25 1z" fill="#fff"/></svg></span>(702) 555-0148</div>
  <div class="contact-item" style="left:392px"><span class="ico"><svg width="12" height="12" viewBox="0 0 24 24"><path d="M3 5h18v14H3z" fill="#fff"/><path d="M3 5l9 8 9-8" stroke="#f8a11b" stroke-width="2" fill="none"/></svg></span>service@coralbaypoolslv.com</div>
  <span class="social" role="img" aria-label="Social link" style="left:877px"></span>
  <span class="social" role="img" aria-label="Social link" style="left:920px"></span>
  <span class="social" role="img" aria-label="Social link" style="left:963px"></span>
  <div class="rule" style="top:3676px"></div>
  <p class="centered" style="top:3697px;font-size:13px;color:#e4e8ee">©2026 Coral Bay Pools - All rights reserved.</p>
</footer>

</div>
</body>
</html>
```